Copper Ridge Inquiries Letterhead

I would like to design a letterhead for a private investigation company. Our primary clients will be law firms. The business card is included below

```html
<!DOCTYPE html>
<html lang="en">
<head>
<meta charset="utf-8">
<title>Copper Ridge Inquiries Letterhead</title>
<link rel="stylesheet" href="https://fonts.googleapis.com/css2?family=Montserrat:wght@300;400;700&family=Lato:wght@400&family=Italianno&display=swap">
<style>
  :root {
    --navy: #1b355f;
    --orange: #ee5a2c;
    --ink: #262626;
    --muted: #3a3a3a;
    --paper: #ffffff;
    --backdrop: #e8e8e8;
  }
  * { box-sizing: border-box; margin: 0; padding: 0; }
  html, body { width: 1200px; height: 960px; overflow: hidden; }
  body { background: var(--backdrop); position: relative; }

  .letterhead {
    position: absolute; left: 282px; top: 30px;
    width: 636px; height: 900px;
    background: var(--paper);
    box-shadow: 0 6px 24px rgba(0,0,0,0.12);
    overflow: hidden;
  }
  .header-swoosh { position: absolute; left: 0; top: 0; width: 636px; height: 150px; display: block; }

  .brand {
    position: absolute; right: 38px; top: 24px;
    display: flex; align-items: center; gap: 9px;
  }
  .brand-dot { width: 14px; height: 14px; border-radius: 50%; background: var(--orange); }
  .brand-name {
    font-family: "Montserrat", sans-serif; font-weight: 700;
    font-size: 14px; line-height: 1.15; letter-spacing: 0.04em;
    color: #ffffff; text-transform: uppercase;
  }

  .contact {
    position: absolute; left: 44px; top: 134px;
    list-style: none;
    font-family: "Montserrat", sans-serif; font-weight: 300;
    font-size: 9.5px; line-height: 13px; letter-spacing: 0.03em;
    color: var(--muted); text-transform: uppercase;
  }
  .contact li { display: flex; align-items: center; gap: 6px; }
  .contact svg { width: 8px; height: 8px; flex: none; }
  .contact .no-icon { padding-left: 14px; }

  .letter {
    position: absolute; left: 52px; top: 228px; right: 62px;
    color: var(--ink);
  }
  .letter-date, .recipient {
    font-family: "Montserrat", sans-serif; font-weight: 400;
    font-size: 12.5px; line-height: 15px;
  }
  .letter-date { margin-bottom: 10px; }
  .recipient { margin-bottom: 10px; }
  .salutation {
    font-family: "Montserrat", sans-serif; font-weight: 700;
    font-size: 15px; margin: 6px 0 10px;
  }
  .letter-body p {
    font-family: "Lato", sans-serif; font-size: 11px; line-height: 15px;
    margin-bottom: 15px;
  }
  .closing {
    font-family: "Montserrat", sans-serif; font-size: 11.5px;
    margin-top: 22px;
  }
  .signature {
    font-family: "Italianno", cursive; font-size: 46px;
    color: #111111; margin: 36px 0 0 70px; line-height: 1;
  }
</style>
</head>
<body>
  <main class="letterhead">
    <svg class="header-swoosh" viewBox="0 0 636 150" aria-hidden="true">
      <path fill="var(--navy)" d="M0 0 H636 V34 C540 66 420 92 280 100 C170 106 70 98 0 92 Z"/>
      <path fill="var(--orange)" d="M0 100 C80 104 180 112 290 106 C420 98 540 70 612 44 C530 80 420 108 290 118 C170 126 70 118 0 116 Z"/>
      <path fill="var(--navy)" d="M228 128 C390 126 530 90 636 46 V88 C520 122 380 136 228 128 Z"/>
    </svg>

    <div class="brand">
      <span class="brand-dot"></span>
      <span class="brand-name">Copper Ridge<br>Inquiries</span>
    </div>

    <ul class="contact">
      <li>
        <svg viewBox="0 0 10 10"><path fill="var(--orange)" d="M5 0.5a3.3 3.3 0 0 0-3.3 3.3C1.7 6.3 5 9.5 5 9.5s3.3-3.2 3.3-5.7A3.3 3.3 0 0 0 5 0.5zm0 4.6a1.3 1.3 0 1 1 0-2.6 1.3 1.3 0 0 1 0 2.6z"/></svg>
        Cedar Hollow, TX
      </li>
      <li>
        <svg viewBox="0 0 10 10"><path fill="var(--orange)" d="M2.2 0.8l1.6 1.9-0.9 1.2c0.6 1.3 1.6 2.3 2.9 2.9l1.2-0.9 1.9 1.6-0.8 1.5C4.7 9 1 5.3 0.8 1.6z"/></svg>
        512.555.0147
      </li>
      <li>
        <svg viewBox="0 0 10 10"><rect x="0.8" y="2" width="8.4" height="6" rx="0.8" fill="var(--orange)"/><path d="M1.2 2.6L5 5.4 8.8 2.6" stroke="#fff" stroke-width="0.8" fill="none"/></svg>
        daniel@copperridgeinquiries.com
      </li>
      <li class="no-icon">License No. 04271936</li>
    </ul>

    <article class="letter">
      <p class="letter-date">January-03-2020</p>
      <p class="recipient">Mr. John Doe<br>President</p>
      <p class="recipient">Fieldstone Corporation<br>123 Street Name, Suite# 10<br>City, State, 120023</p>
      <p class="salutation">Dear Mr. John</p>
      <div class="letter-body">
        <p>Lorem ipsum dolor sit amet, consectetur adipiscing elit, sed do eiusmod tempor incididunt ut labore et dolore magna aliqua. Ut enim ad minim veniam, quis nostrud exercitation ullamco laboris nisi ut aliquip ex ea commodo consequat. Duis aute irure dolor in reprehenderit in voluptate velit esse cillum dolore eu fugiat nulla pariatur.</p>
        <p>Lorem ipsum dolor sit amet, consectetur adipiscing elit, sed do eiusmod tempor incididunt ut labore et dolore magna aliqua. Ut enim ad minim veniam, quis nostrud exercitation ullamco laboris nisi ut aliquip ex ea commodo consequat. Duis aute irure dolor in reprehenderit in voluptate velit esse cillum dolore eu fugiat nulla pariatur.</p>
        <p>Lorem ipsum dolor sit amet, consectetur adipiscing elit, sed do eiusmod tempor incididunt ut labore et dolore magna aliqua. Ut enim ad minim veniam, quis nostrud exercitation ullamco laboris nisi ut aliquip ex ea commodo consequat.</p>
        <p>Excepteur sint occaecat cupidatat non proident, sunt in culpa qui officia deserunt mollit anim id est laborum. re et dolore magnam aliquam quaerat voluptatem.</p>
      </div>
      <p class="closing">Regards</p>
      <p class="signature">Daniel Hart</p>
    </article>
  </main>
</body>
</html>
```